Voranta Imports Busisness cards and logo

Voranta imports is a brand new wholesale company located in Londonderry, New Hampshire dedicated to finding unique products from around the world.
Licensed to sell wine and spirits in the state and also authorized distributors of Pale Meadow Design, a manufacturer of girls and women shoes. Other products that we are currently trying to import are cheese and frozen food from Spain.
We would like a design that portraits our diversity of products and wholesale capabilities

```html
<!DOCTYPE html>
<html lang="en">
<head>
<meta charset="utf-8">
<title>Voranta Imports – Business Cards</title>
<link href="https://fonts.googleapis.com/css2?family=Play:wght@400;700&display=swap" rel="stylesheet">
<style>
  :root {
    --backdrop: #8f9192;
    --card: #f6f7f6;
    --green-deep: #1e6f26;
    --green-mid: #2f8f34;
    --green-bright: #6cbf2a;
    --green-text: #2aa24a;
    --ink: #3a3d3f;
    --ink-soft: #6b6f72;
  }
  * { margin: 0; padding: 0; box-sizing: border-box; }
  html, body {
    width: 1200px; height: 894px; overflow: hidden;
    background: var(--backdrop);
    font-family: "Play", sans-serif;
  }
  .canvas { position: relative; width: 1200px; height: 894px; }

  .card {
    position: absolute;
    width: 560px; height: 320px;
    background: var(--card);
    overflow: hidden;
    box-shadow: 0 6px 18px rgba(0,0,0,0.25);
  }
  .card--front { left: 590px; top: 100px; }
  .card--back  { left: 50px;  top: 470px; }

  .band {
    position: absolute; right: 0;
    border-radius: 40px 0 0 40px;
    background: radial-gradient(ellipse at 35% 40%, var(--green-mid), var(--green-deep) 75%);
  }
  .card--front .band { left: 300px; top: 165px; height: 72px; }
  .card--back  .band { left: 345px; top: 92px;  height: 80px; }

  .brand {
    position: absolute; left: 70px; top: 52px;
    display: flex; flex-direction: column; align-items: center; gap: 10px;
  }
  .brand__mark {
    width: 62px; height: 62px; border-radius: 50%;
    background: var(--green-bright);
  }
  .brand__name {
    font-weight: 700; font-size: 30px; color: var(--green-deep);
    letter-spacing: 0.5px;
  }

  .contact { position: absolute; left: 34px; top: 30px; width: 280px; }
  .contact__name { font-size: 22px; color: var(--green-text); }
  .contact__role {
    font-size: 10px; letter-spacing: 1px; color: var(--ink-soft);
    text-transform: uppercase; margin-top: 1px;
  }
  .rule { height: 2px; background: var(--green-bright); }
  .contact .rule { margin-top: 8px; width: 250px; }
  .details {
    display: grid; grid-template-columns: 64px 1fr;
    row-gap: 4px; margin-top: 12px; font-size: 14px;
  }
  .details dt { color: var(--green-text); }
  .details dd { color: var(--ink); letter-spacing: 0.5px; }

  .address {
    position: absolute; left: 34px; top: 210px;
    display: flex; align-items: center; gap: 10px;
    font-size: 14px; color: var(--ink); letter-spacing: 0.5px;
  }
  .rule--long { position: absolute; left: 34px; width: 470px; }
  .rule--a { top: 200px; }
  .rule--b { top: 240px; }

  .back-mark {
    position: absolute; left: 360px; top: 205px;
    width: 84px; height: 84px; border-radius: 50%;
    background: var(--green-bright);
  }
</style>
</head>
<body>
<main class="canvas">

  <section class="card card--front" aria-label="Business card front">
    <div class="brand">
      <span class="brand__mark"></span>
      <span class="brand__name">Voranta Imports</span>
    </div>
    <div class="band"></div>
  </section>

  <section class="card card--back" aria-label="Business card back">
    <div class="contact">
      <h1 class="contact__name">Daniel Harlow</h1>
      <p class="contact__role">General Manager</p>
      <div class="rule"></div>
      <dl class="details">
        <dt>Phone:</dt><dd>012 345 6789</dd>
        <dt>Fax:</dt><dd>012 345 6789</dd>
        <dt>Email:</dt><dd>urname@email.com</dd>
        <dt>website:</dt><dd>www.companyname.com</dd>
      </dl>
    </div>
    <div class="rule rule--long rule--a"></div>
    <p class="address">
      <svg width="14" height="20" viewBox="0 0 14 20" aria-hidden="true">
        <path d="M7 0C3.1 0 0 3.1 0 7c0 5 7 13 7 13s7-8 7-13c0-3.9-3.1-7-7-7z" fill="#3a8fd0"/>
        <circle cx="7" cy="7" r="2.6" fill="#fff"/>
      </svg>
      27 Harvest Lane, Suite 4, Londonderry NH
    </p>
    <div class="rule rule--long rule--b"></div>
    <div class="band"></div>
    <span class="back-mark"></span>
  </section>

</main>
</body>
</html>
```